Exciting new website for concierge aesthetic company

Simple, elegant, fresh design for female owned concierge aesthetic company, catering to both men and women ages 30-60. We would like a home page with an exciting catch phrase, a brief description of the company and a section to fill out an appointment request that includes a section for a referral. Please also have a book appointment link in the header of all pages that will link back to booking information form on home page. Separate pages to include:
- Services = 3 different services. Each service stating the name of the service and then providing a brief description. 3 services are "Private Session" for 1 client, "Group Session" for 2-5 clients, "Party" for 6+ clients. Will provide service descriptions text later. Item at bottom of page to allow description of how to "Host a Party".
- Products = 4 different product lines. Will provide pictures of product, brief description and link to manufacturer's website.
- Stories = brief client reviews to include before and after photos
- About us = Personal picture with brief description of owner's fun, exciting and family focussed lifestyle.
*Our domain is registered with varnix and we be using varnix for website hosting.

Target Market(s)

30-60 year old men and women, but mostly women

Industry/Entity Type

beauty and aesthetics

Coding

Coded - Design and coding required

Number of Pages Required

5+ page

Font styles to use
Sans Serif
Script

Colors
59FF00
82FF00
B8FF75
E3FFCB
F4FFEA
FFC000
F8CF3A
FAE287
FDF2CF
FEFAEE
F0912C
F2A743
F7CA91
FBE8D2
FDF5EE
E54698
E96AAD
F1A4CE
F9D9EA
FCEFF6

Requirements
Must have
• coded for varnix
Should not have
• corny pictures. No needles in pictures or graphics. No medical office or medical chair in pictures.

```html
<!DOCTYPE html>
<html lang="en">
<head>
<meta charset="UTF-8">
<title>Glow Belle – Concierge Aesthetics</title>
<link href="https://fonts.googleapis.com/css2?family=Dancing+Script:wght@500;700&family=Raleway:wght@400;500&display=swap" rel="stylesheet">
<style>
:root{
  --pink:#e5358f;
  --pink-soft:#f1a4ce;
  --orange:#f0792c;
  --orange-soft:#f2a743;
  --hero-bg:#d5dce4;
  --cream:#f3e9da;
  --cream-light:#f7efe4;
  --ink:#2a2a2a;
  --muted:#6b6b6b;
  --dark:#232323;
  --white:#ffffff;
}
*{margin:0;padding:0;box-sizing:border-box}
html,body{width:1200px;height:3734px;overflow:hidden;background:var(--white)}
body{font-family:'Raleway',sans-serif;color:var(--ink)}
.page{position:relative;width:1200px;height:3734px;overflow:hidden}
.abs{position:absolute}
.script{font-family:'Dancing Script',cursive}
.layer-bg{z-index:0}
.waves{position:absolute;left:0;top:0;z-index:1}
.content{z-index:2}

/* header */
.site-header{left:0;top:0;width:1200px;height:107px;background:var(--white);z-index:3}
.brand{left:113px;top:24px;display:flex;align-items:center;gap:12px}
.brand-mark{width:46px;height:46px;border-radius:50%;background:var(--pink-soft)}
.brand-name{font-family:'Dancing Script',cursive;font-weight:700;font-size:40px;color:var(--pink);line-height:1}
.brand-tag{font-size:9px;letter-spacing:5px;color:var(--orange);margin-top:4px}
.nav{left:445px;top:44px;display:flex;gap:40px;font-size:15px}
.nav a{color:var(--ink);text-decoration:none}
.btn{display:inline-flex;align-items:center;justify-content:center;background:var(--pink);color:var(--white);font-family:'Dancing Script',cursive;font-weight:700;text-decoration:none;border-radius:22px 0 22px 0}
.btn-book{left:907px;top:28px;width:180px;height:56px;font-size:19px}

/* hero */
.hero-bg{left:0;top:107px;width:1200px;height:760px;background:var(--hero-bg)}
.hero-photo{left:520px;top:107px;width:680px;height:720px;background:radial-gradient(ellipse at 55% 40%,#e9c3a6 0%,#d9a98a 30%,#cfd5dc 72%)}
.hero-title{left:113px;top:300px;font-family:'Dancing Script',cursive;font-weight:700;font-size:96px;color:var(--orange);line-height:1}
.hero-tag{left:113px;top:415px;font-size:18px;letter-spacing:14px;color:var(--orange)}
.btn-hero{left:261px;top:481px;width:137px;height:56px;font-size:19px}
.arrow{top:445px;width:24px;height:40px}
.dots{left:578px;top:699px;display:flex;gap:6px}
.dots span{width:10px;height:10px;border-radius:50%;background:#b9bec4}
.dots span.on{background:var(--orange)}

/* headings */
.section-title{width:1200px;left:0;text-align:center;font-family:'Dancing Script',cursive;font-weight:700;font-size:40px;color:var(--pink)}
.section-title span{color:var(--orange)}

/* products */
.product{top:996px;width:230px;height:380px;background:var(--white);box-shadow:0 2px 10px rgba(0,0,0,.12);text-align:center}
.product-img{margin:9px 9px 0;height:165px}
.product h3{font-family:'Dancing Script',cursive;font-weight:700;font-size:21px;margin-top:16px}
.product p{font-size:12.5px;line-height:21px;color:var(--muted);padding:0 22px;margin-top:10px}
.btn-outline{display:inline-flex;align-items:center;justify-content:center;margin-top:16px;width:128px;height:53px;border:1.5px solid var(--pink);color:var(--pink);font-family:'Dancing Script',cursive;font-size:19px;border-radius:20px 0 20px 0}
.product.active{background:var(--pink)}
.product.active h3,.product.active p{color:var(--white)}
.product.active .btn-outline{color:var(--white);border-color:var(--white)}

/* about */
.about-photo{left:158px;top:1630px;width:420px;height:420px;border-radius:50%;background:radial-gradient(circle at 50% 45%,#e8cfc0 0%,#b9a9a2 45%,#8d8d90 100%);border-bottom:7px solid var(--orange)}
.about-title{left:684px;top:1630px;font-family:'Dancing Script',cursive;font-weight:700;font-size:40px;color:var(--pink)}
.about-text{left:684px;top:1703px;width:400px;font-size:13.5px;line-height:25.7px;color:var(--muted);text-align:justify}
.btn-about{left:684px;top:1962px;width:137px;height:54px;font-size:19px}

/* services */
.service{top:2365px;width:227px;height:237px;border:2px solid var(--orange-soft);background:var(--white);text-align:center}
.service svg{margin-top:38px}
.service h3{font-family:'Dancing Script',cursive;font-weight:500;font-size:23px;margin-top:14px}
.service p{font-size:12.5px;line-height:22px;color:var(--muted);margin-top:6px}

/* stories */
.story{top:2930px;width:471px;height:257px;border-radius:14px}
.story-1{left:111px;background:linear-gradient(90deg,#e7e9ee 0%,#cfa88f 40%,#d8b39b 60%,#e7ebef 100%)}
.story-2{left:617px;background:linear-gradient(90deg,#e5c9b1 0%,#c9a48a 45%,#d9bca5 100%)}

/* footer */
.footer-brand{left:111px;top:3470px;width:270px;text-align:center}
.footer-brand .brand-mark{width:80px;height:80px;margin:0 auto 18px}
.footer-brand .brand-name{font-size:54px;color:var(--orange)}
.footer-brand .brand-tag{font-size:11px;letter-spacing:7px;color:var(--pink);margin-top:10px}
.footer-col{top:3432px;color:var(--white)}
.footer-col h4{font-family:'Dancing Script',cursive;font-weight:500;font-size:25px;margin-bottom:20px}
.footer-col li{list-style:none;font-size:15px;line-height:26px}
.footer-rule{left:111px;top:3640px;width:976px;height:1px;background:#444}
.copyright{left:111px;top:3666px;color:var(--white);font-size:15px}
.social{left:960px;top:3668px;display:flex;gap:14px;font-size:12px;color:var(--orange);align-items:center}
</style>
</head>
<body>
<div class="page">

  <!-- background blocks -->
  <div class="abs hero-bg layer-bg"></div>
  <div class="abs hero-photo layer-bg" role="img" aria-label="Smiling woman touching her cheek"></div>

  <svg class="waves" width="1200" height="3734" viewBox="0 0 1200 3734" aria-hidden="true">
    <defs>
      <linearGradient id="pinkOrange" x1="0" x2="1" y1="0" y2="0">
        <stop offset="0" stop-color="#e5358f"/>
        <stop offset="1" stop-color="#f0792c"/>
      </linearGradient>
    </defs>
    <!-- hero bottom -->
    <path d="M0 765 C200 845 420 840 620 775 C820 710 1000 690 1200 790 V880 H0 Z" fill="#fff"/>
    <path d="M0 765 C200 845 420 840 620 775 C820 710 1000 690 1200 790" fill="none" stroke="url(#pinkOrange)" stroke-width="9"/>
    <!-- about band -->
    <path d="M0 1510 C220 1590 460 1570 720 1495 C930 1435 1080 1450 1200 1530 L1200 2140 C1050 2050 860 2055 640 2115 C420 2175 200 2195 0 2120 Z" fill="#f3e9da"/>
    <path d="M0 1510 C220 1590 460 1570 720 1495 C930 1435 1080 1450 1200 1530" fill="none" stroke="url(#pinkOrange)" stroke-width="9"/>
    <path d="M0 2120 C200 2195 420 2175 640 2115 C860 2055 1050 2050 1200 2140" fill="none" stroke="url(#pinkOrange)" stroke-width="9"/>
    <!-- stories band -->
    <path d="M0 2720 C220 2800 460 2780 720 2705 C930 2645 1080 2650 1200 2740 L1200 3300 H0 Z" fill="#f7efe4"/>
    <path d="M0 2720 C220 2800 460 2780 720 2705 C930 2645 1080 2650 1200 2740" fill="none" stroke="url(#pinkOrange)" stroke-width="9"/>
    <!-- footer -->
    <path d="M0 3300 C200 3365 420 3350 640 3290 C860 3230 1050 3225 1200 3275 V3734 H0 Z" fill="#232323"/>
    <path d="M0 3300 C200 3365 420 3350 640 3290 C860 3230 1050 3225 1200 3275" fill="none" stroke="url(#pinkOrange)" stroke-width="9"/>
  </svg>

  <!-- header -->
  <header class="abs site-header">
    <div class="abs brand">
      <div class="brand-mark"></div>
      <div>
        <div class="brand-name">Glow Belle</div>
        <div class="brand-tag">CONCIERGE AESTHETICS</div>
      </div>
    </div>
    <nav class="abs nav">
      <a href="#">Home</a><a href="#">About</a><a href="#">Services</a><a href="#">Products</a><a href="#">Stories</a>
    </nav>
    <a class="abs btn btn-book" href="#">Book Appointment</a>
  </header>

  <!-- hero -->
  <section class="content">
    <h1 class="abs hero-title content">Glow Belle</h1>
    <div class="abs hero-tag content">CONCIERGE AESTHETICS</div>
    <a class="abs btn btn-hero content" href="#">Get Started</a>
    <svg class="abs arrow content" style="left:45px" viewBox="0 0 24 40"><path d="M20 4 L6 20 L20 36" fill="none" stroke="#eef0f3" stroke-width="4"/></svg>
    <svg class="abs arrow content" style="left:1125px" viewBox="0 0 24 40"><path d="M4 4 L18 20 L4 36" fill="none" stroke="#f0792c" stroke-width="4"/></svg>
    <div class="abs dots content"><span></span><span class="on"></span><span></span></div>
  </section>

  <!-- products -->
  <section class="content">
    <h2 class="abs section-title content" style="top:910px">Our <span>Products</span></h2>
    <article class="abs product content" style="left:111px">
      <div class="product-img" role="img" aria-label="Aesthetician treating a client" style="background:linear-gradient(135deg,#e9e4df,#c7b6a6)"></div>
      <h3>Lorem ipsum dolor</h3>
      <p>Lorem ipsum dolor sit amet, consectetur adipiscing elit, sed aliqua.</p>
      <span class="btn-outline">View Details</span>
    </article>
    <article class="abs product active content" style="left:359px">
      <div class="product-img" role="img" aria-label="Client receiving a facial mask" style="background:linear-gradient(135deg,#f3eeea,#d9c5b6)"></div>
      <h3>Lorem ipsum dolor</h3>
      <p>Lorem ipsum dolor sit amet, consectetur adipiscing elit, sed aliqua.</p>
      <span class="btn-outline">View Details</span>
    </article>
    <article class="abs product content" style="left:609px">
      <div class="product-img" role="img" aria-label="Smiling client during consultation" style="background:linear-gradient(135deg,#6fa4a6,#d7b29a)"></div>
      <h3>Lorem ipsum dolor</h3>
      <p>Lorem ipsum dolor sit amet, consectetur adipiscing elit, sed aliqua.</p>
      <span class="btn-outline">View Details</span>
    </article>
    <article class="abs product content" style="left:857px">
      <div class="product-img" role="img" aria-label="Relaxing face massage" style="background:linear-gradient(135deg,#efe8e2,#dcbfa8)"></div>
      <h3>Lorem ipsum dolor</h3>
      <p>Lorem ipsum dolor sit amet, consectetur adipiscing elit, sed aliqua.</p>
      <span class="btn-outline">View Details</span>
    </article>
  </section>

  <!-- about -->
  <section class="content">
    <div class="abs about-photo content" role="img" aria-label="Woman with gloved hands framing her face"></div>
    <h2 class="abs about-title content">About Us</h2>
    <p class="abs about-text content">Sed ut perspiciatis unde omnis iste natus error sit voluptatem accu santium doloremque laudantium, totam rem aperiam, eaque ipsa quae ab illo inventore veritatis et quasi architecto beatae vitae dicta sunt explicabo. Nemo enim ipsam voluptatem quia voluptas sit aspernatur aut odit aut fugit, sed quia consequuntur magni dolores eos qui ratione voluptatem sequi nesciunt. Neque porro quisquam est, qui dolorem ipsum quia dolor sit amet, consectetur, adipisci velit, sed quia non magnam aliquam quaerat voluptatem.</p>
    <a class="abs btn btn-about content" href="#">Get Started</a>
  </section>

  <!-- services -->
  <section class="content">
    <h2 class="abs section-title content" style="top:2260px">Our <span>Services</span></h2>
    <article class="abs service content" style="left:223px">
      <svg width="60" height="70" viewBox="0 0 60 70"><circle cx="30" cy="16" r="12" fill="none" stroke="#e5358f" stroke-width="3"/><path d="M6 66 V54 C6 42 18 36 30 36 C42 36 54 42 54 54 V66 Z" fill="none" stroke="#e5358f" stroke-width="3"/></svg>
      <h3>Private Session</h3>
      <p>Lorem ipsum dolor sit amet,<br>consectetur adipiscing</p>
    </article>
    <article class="abs service content" style="left:486px">
      <svg width="100" height="70" viewBox="0 0 100 70"><circle cx="50" cy="18" r="11" fill="none" stroke="#e5358f" stroke-width="3"/><circle cx="22" cy="22" r="9" fill="none" stroke="#e5358f" stroke-width="3"/><circle cx="78" cy="22" r="9" fill="none" stroke="#e5358f" stroke-width="3"/><path d="M4 64 V54 C4 44 12 38 22 38 C32 38 40 44 40 54" fill="none" stroke="#e5358f" stroke-width="3"/><path d="M60 54 C60 44 68 38 78 38 C88 38 96 44 96 54 V64" fill="none" stroke="#e5358f" stroke-width="3"/><path d="M28 66 V52 C28 42 38 36 50 36 C62 36 72 42 72 52 V66 Z" fill="none" stroke="#e5358f" stroke-width="3"/></svg>
      <h3>Group Session</h3>
      <p>Lorem ipsum dolor sit amet,<br>consectetur adipiscing</p>
    </article>
    <article class="abs service content" style="left:749px">
      <svg width="100" height="84" viewBox="0 0 100 84" style="margin-top:28px"><circle cx="50" cy="10" r="8" fill="none" stroke="#e5358f" stroke-width="3"/><circle cx="30" cy="14" r="7" fill="none" stroke="#e5358f" stroke-width="3"/><circle cx="70" cy="14" r="7" fill="none" stroke="#e5358f" stroke-width="3"/><circle cx="50" cy="32" r="10" fill="none" stroke="#e5358f" stroke-width="3"/><circle cx="20" cy="36" r="8" fill="none" stroke="#e5358f" stroke-width="3"/><circle cx="80" cy="36" r="8" fill="none" stroke="#e5358f" stroke-width="3"/><path d="M4 78 V68 C4 58 12 50 22 50" fill="none" stroke="#e5358f" stroke-width="3"/><path d="M78 50 C88 50 96 58 96 68 V78" fill="none" stroke="#e5358f" stroke-width="3"/><path d="M26 80 V66 C26 56 38 48 50 48 C62 48 74 56 74 66 V80 Z" fill="none" stroke="#e5358f" stroke-width="3"/></svg>
      <h3>Party</h3>
      <p>Lorem ipsum dolor sit amet,<br>consectetur adipiscing</p>
    </article>
  </section>

  <!-- stories -->
  <section class="content">
    <h2 class="abs section-title content" style="top:2828px">Our <span>Stories</span></h2>
    <div class="abs story story-1 content" role="img" aria-label="Before and after comparison of facial skin"></div>
    <div class="abs story story-2 content" role="img" aria-label="Before and after comparison of eye area"></div>
  </section>

  <!-- footer -->
  <footer class="content">
    <div class="abs footer-brand content">
      <div class="brand-mark"></div>
      <div class="brand-name">Glow Belle</div>
      <div class="brand-tag">CONCIERGE AESTHETICS</div>
    </div>
    <div class="abs footer-col content" style="left:486px">
      <h4>Quick Links</h4>
      <ul><li>Home</li><li>About</li><li>Services</li><li>Products</li><li>Stories</li></ul>
    </div>
    <div class="abs footer-col content" style="left:725px">
      <h4>Service</h4>
      <ul><li>Private Session</li><li>Group Session</li><li>Party</li></ul>
    </div>
    <div class="abs footer-col content" style="left:950px">
      <h4>Conditions</h4>
      <ul><li>Delivery</li><li>Terms of Conditions</li><li>Privacy policy</li></ul>
    </div>
    <div class="abs footer-rule content"></div>
    <div class="abs copyright content">Copyrights 2022 Glow Belle &nbsp;|&nbsp;&nbsp; All Rights Reserved</div>
    <div class="abs social content"><span>Pulse</span><span>Frame</span><span>Linkr</span><span>Reel</span></div>
  </footer>

</div>
</body>
</html>
```